Quiet Lanterns for the Restless Inner Mind

I would like a website designed that would be used to upload podcasts, videos and written material about mental health. Where people will be being as honest, open and truthful as they can about mental health issues.
I would like it to look calming and soothing. Inspired by Dorlac's paintings and colour schemes.

I am on Brightlane as Dr Helen Maddox - and chirpbox as drhelenmaddox

Target Market(s)

Healthcare professionals and users of services who want to think at a deeper level about the nature of mental illness

Number of Pages Required

1 page

```html
<!DOCTYPE html>
<html lang="en">
<head>
<meta charset="utf-8">
<title>Dr Helen Maddox</title>
<link href="https://fonts.googleapis.com/css2?family=Poppins:wght@200;300;400;500;600;700&display=swap" rel="stylesheet">
<style>
:root{
  --teal:#6fd0cf;
  --orange:#d89a2e;
  --beige:#e2d7b3;
  --grey:#f3f3f3;
  --navy:#1c2a5b;
  --ink:#333333;
  --muted:#555555;
  --mic:#e0533a;
  --white:#ffffff;
}
*{margin:0;padding:0;box-sizing:border-box}
html,body{width:1200px;height:4615px;overflow:hidden}
body{font-family:'Poppins',sans-serif;color:var(--ink);background:var(--white);position:relative}
section,header,footer{position:absolute;left:0;width:1200px}
.abs{position:absolute}
.btn{position:absolute;background:var(--teal);color:var(--white);font-size:15px;font-weight:400;letter-spacing:.5px;display:flex;align-items:center;justify-content:center;text-transform:uppercase}
.heading{position:absolute;font-weight:200;text-transform:uppercase;font-size:66px;line-height:1.1;color:#222;letter-spacing:1px}
.body-text{position:absolute;font-size:14.5px;line-height:29.5px;color:var(--muted)}
.body-text p+p{margin-top:14px}
.media{position:absolute}
.beige-block{position:absolute;background:var(--beige)}
.orange-bracket{position:absolute;border-right:15px solid var(--orange);border-bottom:15px solid var(--orange)}
.orange-bracket.left{border-right:none;border-left:15px solid var(--orange)}
.arrows{position:absolute;display:flex;gap:16px}

/* hero */
.hero{top:0;height:738px;background:linear-gradient(135deg,#3a4a6a 0%,#2b3a5c 45%,#1f2c4c 100%)}
.hero .logo{left:75px;top:66px;font-size:29px;font-weight:700;color:var(--white);letter-spacing:.3px}
.nav{position:absolute;left:534px;top:76px;display:flex;gap:34px;font-size:12.5px;font-weight:600;color:var(--white)}
.nav .active{text-decoration:underline;text-underline-offset:5px}
.social{position:absolute;display:flex;gap:14px;align-items:center;font-size:13px;font-weight:600}
.hero .social{left:1058px;top:74px;color:var(--white)}
.social span::before{content:"";display:inline-block;width:8px;height:8px;background:currentColor;margin-right:5px;vertical-align:middle}
.hero-title{left:72px;top:462px;font-size:56px;font-weight:400;color:var(--white);letter-spacing:1px}
.hero-sub{left:74px;top:535px;font-size:28px;font-weight:400;color:var(--white)}

/* about */
.about{top:738px;height:716px;background:var(--white)}

/* podcast */
.podcast{top:1454px;height:505px;background:var(--grey)}
.card{position:absolute;top:158px;width:242px;height:178px;background:var(--white);box-shadow:0 1px 4px rgba(0,0,0,.08);padding:16px 20px}
.card h3{font-size:18px;font-weight:400;color:var(--orange);margin-bottom:6px}
.card p{font-size:14px;line-height:25px;color:var(--muted)}
.card .dur{margin-top:12px;font-size:14px;color:var(--mic);display:flex;align-items:center;gap:8px}

/* mental */
.mental{top:1959px;height:704px;background:var(--white)}

/* videos */
.videos{top:2663px;height:552px;background:var(--grey)}
.thumb{position:absolute;top:160px;width:328px;height:220px}
.thumb svg{position:absolute;left:144px;top:90px}

/* testimonials */
.testimonials{top:3215px;height:525px;background:var(--white)}
.avatar{position:absolute;border-radius:50%}
.quote{position:absolute;left:180px;width:840px;top:308px;text-align:center;font-size:16.5px;line-height:36px;color:var(--muted)}
.name{position:absolute;left:0;width:1200px;top:432px;text-align:center;font-size:15px;font-weight:500;color:var(--orange);letter-spacing:.5px}

/* contact */
.contact{top:3740px;height:677px;background:var(--grey)}
.field{position:absolute;background:var(--white);border:1px solid #c9c9c9;font-size:13px;color:#666;padding:20px 16px 0}

/* footer */
.footer{top:4417px;height:198px;background:var(--navy);color:var(--white)}
.footer .nav{left:363px;top:46px;gap:32px;font-size:13px}
.copyright{position:absolute;left:0;width:1200px;top:74px;text-align:center;font-size:13px}
.footer .social{left:540px;top:124px}
</style>
</head>
<body>

<header class="hero">
  <div class="media" role="img" aria-label="Photo of a group therapy session with a counsellor and participants seated in a circle" style="left:0;top:0;width:1200px;height:738px;background:linear-gradient(135deg,#4a5a78 0%,#34436a 50%,#22304f 100%)"></div>
  <div class="abs logo">DR HELEN MADDOX</div>
  <nav class="nav"><span class="active">HOME</span><span>ABOUT ME</span><span>PADCASTS</span><span>VIDEOS</span><span>CONTACT US</span></nav>
  <div class="social"><span>Brightlane</span><span>chirpbox</span></div>
  <h1 class="abs hero-title">DR HELEN MADDOX</h1>
  <div class="abs hero-sub">Quiet Lanterns for the Restless Inner Mind</div>
  <div class="btn" style="left:75px;top:595px;width:179px;height:59px">Read More</div>
</header>

<section class="about">
  <div class="beige-block" style="left:61px;top:82px;width:295px;height:285px"></div>
  <div class="orange-bracket" style="left:405px;top:448px;width:182px;height:177px"></div>
  <div class="media" role="img" aria-label="Portrait photo of Dr Helen Maddox" style="left:98px;top:123px;width:473px;height:484px;background:linear-gradient(160deg,#2a1d18 0%,#6b4232 50%,#2a1a14 100%)"></div>
  <h2 class="heading" style="left:614px;top:108px">About Me</h2>
  <div class="body-text" style="left:616px;top:208px;width:520px">
    <p>Sed ut perspiciatis unde omnis iste natus error sit voluptatem accusantium doloremque laudantium, totam rem aperiam, eaque ipsa quae ab illo inventore veritatis et quasi architecto beatae vitae dicta sunt explicabo. Nemo enim ipsam voluptatem quia voluptas sit aspernatur aut odit aut fugit, sed quia consequuntur magni dolores.</p>
    <p>Sed ut perspiciatis unde omnis iste natus error sit voluptatem accusantium doloremque laudantium, totam rem aperiam, eaque ipsa quae ab illo inventore veritatis et quasi architecto beatae vitae dicta sunt explicabo.</p>
  </div>
  <div class="btn" style="left:616px;top:548px;width:177px;height:59px">Read More</div>
</section>

<section class="podcast">
  <h2 class="heading" style="left:70px;top:50px">Podcast</h2>
  <div class="arrows" style="left:1056px;top:70px">
    <svg width="28" height="24" viewBox="0 0 28 24"><path d="M26 12H4M13 3L3 12l10 9" fill="none" stroke="#8a8a8a" stroke-width="3.5"/></svg>
    <svg width="28" height="24" viewBox="0 0 28 24"><path d="M2 12h22M15 3l10 9-10 9" fill="none" stroke="#d89a2e" stroke-width="3.5"/></svg>
  </div>
  <div class="card" style="left:75px"><h3>Sed ut perspiciatis</h3><p>Unde omnis iste natus er ror sit voluptatem sint oc caecat cupidatat.</p><div class="dur"><svg width="10" height="16" viewBox="0 0 10 16"><rect x="2.5" y="0" width="5" height="10" rx="2.5" fill="#e0533a"/><path d="M1 7a4 4 0 0 0 8 0M5 11v4" fill="none" stroke="#e0533a" stroke-width="1.5"/></svg>2:30 Min</div></div>
  <div class="card" style="left:342px"><h3>Sed ut perspiciatis</h3><p>Unde omnis iste natus er ror sit voluptatem sint oc caecat cupidatat.</p><div class="dur"><svg width="10" height="16" viewBox="0 0 10 16"><rect x="2.5" y="0" width="5" height="10" rx="2.5" fill="#e0533a"/><path d="M1 7a4 4 0 0 0 8 0M5 11v4" fill="none" stroke="#e0533a" stroke-width="1.5"/></svg>2:30 Min</div></div>
  <div class="card" style="left:614px"><h3>Sed ut perspiciatis</h3><p>Unde omnis iste natus er ror sit voluptatem sint oc caecat cupidatat.</p><div class="dur"><svg width="10" height="16" viewBox="0 0 10 16"><rect x="2.5" y="0" width="5" height="10" rx="2.5" fill="#e0533a"/><path d="M1 7a4 4 0 0 0 8 0M5 11v4" fill="none" stroke="#e0533a" stroke-width="1.5"/></svg>2:30 Min</div></div>
  <div class="card" style="left:885px"><h3>Sed ut perspiciatis</h3><p>Unde omnis iste natus er ror sit voluptatem sint oc caecat cupidatat.</p><div class="dur"><svg width="10" height="16" viewBox="0 0 10 16"><rect x="2.5" y="0" width="5" height="10" rx="2.5" fill="#e0533a"/><path d="M1 7a4 4 0 0 0 8 0M5 11v4" fill="none" stroke="#e0533a" stroke-width="1.5"/></svg>2:30 Min</div></div>
  <div class="btn" style="left:485px;top:389px;width:231px;height:59px">Listen All Podcasts</div>
</section>

<section class="mental">
  <h2 class="heading" style="left:72px;top:108px">About Mental<br>Health Issues</h2>
  <div class="body-text" style="left:75px;top:268px;width:520px">
    <p>Sed ut perspiciatis unde omnis iste natus error sit voluptatem accusantium doloremque laudantium, totam rem aperiam, eaque ipsa quae ab illo inventore veritatis et quasi architecto beatae vitae dicta sunt explicabo. Nemo enim ipsam voluptatem quia voluptas sit aspernatur aut odit aut fugit, sed quia consequuntur magni dolores.</p>
    <p>Sed ut perspiciatis unde omnis iste natus error sit voluptatem accusantium doloremque laudantium.</p>
  </div>
  <div class="btn" style="left:75px;top:545px;width:179px;height:59px">Read More</div>
  <div class="beige-block" style="left:867px;top:79px;width:297px;height:283px"></div>
  <div class="orange-bracket left" style="left:637px;top:444px;width:183px;height:178px"></div>
  <div class="media" role="img" aria-label="Photo of a therapist talking with a client in a bright consulting room" style="left:652px;top:120px;width:473px;height:484px;background:linear-gradient(135deg,#d9ded8 0%,#b9c3bd 50%,#8f9c8c 100%)"></div>
</section>

<section class="videos">
  <h2 class="heading" style="left:70px;top:52px">Videos</h2>
  <div class="arrows" style="left:1056px;top:72px">
    <svg width="28" height="24" viewBox="0 0 28 24"><path d="M26 12H4M13 3L3 12l10 9" fill="none" stroke="#8a8a8a" stroke-width="3.5"/></svg>
    <svg width="28" height="24" viewBox="0 0 28 24"><path d="M2 12h22M15 3l10 9-10 9" fill="none" stroke="#d89a2e" stroke-width="3.5"/></svg>
  </div>
  <div class="thumb" role="img" aria-label="Video still of a counsellor taking notes in an office" style="left:75px;background:linear-gradient(135deg,#e6dfd4 0%,#c9b8a3 60%,#9a8572 100%)"><svg width="40" height="40" viewBox="0 0 40 40"><circle cx="20" cy="20" r="17" fill="rgba(255,255,255,.25)" stroke="#fff" stroke-width="3"/><path d="M16 12l12 8-12 8z" fill="#fff"/></svg></div>
  <div class="thumb" role="img" aria-label="Video still of two women in conversation on a sofa" style="left:437px;background:linear-gradient(135deg,#eef0f0 0%,#d4d2cc 60%,#aca59b 100%)"><svg width="40" height="40" viewBox="0 0 40 40"><circle cx="20" cy="20" r="17" fill="rgba(255,255,255,.25)" stroke="#fff" stroke-width="3"/><path d="M16 12l12 8-12 8z" fill="#fff"/></svg></div>
  <div class="thumb" role="img" aria-label="Video still of a moody teal and grey painted portrait" style="left:799px;background:linear-gradient(135deg,#3a4a52 0%,#4f7f86 50%,#1f2a30 100%)"><svg width="40" height="40" viewBox="0 0 40 40"><circle cx="20" cy="20" r="17" fill="rgba(255,255,255,.25)" stroke="#fff" stroke-width="3"/><path d="M16 12l12 8-12 8z" fill="#fff"/></svg></div>
  <div class="btn" style="left:485px;top:430px;width:231px;height:59px">View All Videos</div>
</section>

<section class="testimonials">
  <h2 class="heading" style="left:0;width:1200px;text-align:center;top:54px">Testimonials</h2>
  <svg class="abs" style="left:372px;top:212px" width="28" height="24" viewBox="0 0 28 24"><path d="M26 12H4M13 3L3 12l10 9" fill="none" stroke="#8a8a8a" stroke-width="3.5"/></svg>
  <svg class="abs" style="left:794px;top:212px" width="28" height="24" viewBox="0 0 28 24"><path d="M2 12h22M15 3l10 9-10 9" fill="none" stroke="#d89a2e" stroke-width="3.5"/></svg>
  <div class="avatar" role="img" aria-label="Avatar photo of a reviewer" style="left:424px;top:177px;width:94px;height:94px;background:linear-gradient(135deg,#cfe3c8,#6f8a6a)"></div>
  <div class="avatar" role="img" aria-label="Avatar photo of the featured reviewer" style="left:541px;top:165px;width:118px;height:118px;background:linear-gradient(135deg,#eeeeee,#b8b0a8);border:5px solid #e8e8e8"></div>
  <div class="avatar" role="img" aria-label="Avatar photo of a reviewer" style="left:680px;top:177px;width:94px;height:94px;background:linear-gradient(135deg,#f08a3c,#c45a1e)"></div>
  <p class="quote">“ Sed ut perspiciatis unde omnis iste natus error sit voluptatem accusantium doloremque laudantium, totam rem aperiam, eaque ipsa quae ab illo inventore veritatis et quasi architecto beatae vitae dicta sunt explicabo. Nemo enim ipsam voluptatem..”</p>
  <div class="name">NAME HEADING</div>
</section>

<section class="contact">
  <div class="beige-block" style="left:61px;top:66px;width:295px;height:283px"></div>
  <div class="orange-bracket" style="left:405px;top:433px;width:182px;height:174px"></div>
  <div class="media" role="img" aria-label="Illustration of a hand holding a phone showing a distressed person, with the words Need Help" style="left:98px;top:107px;width:473px;height:484px;background:linear-gradient(160deg,#d8ccc8 0%,#cbbdb8 60%,#a9968c 100%)"></div>
  <h2 class="heading" style="left:614px;top:92px">Contact Me</h2>
  <div class="body-text" style="left:616px;top:188px;width:520px"><p>Sed ut perspiciatis unde omnis iste natus error sit voluptatem accusantium doloremque laudantium.</p></div>
  <div class="field" style="left:616px;top:266px;width:249px;height:61px">First Name</div>
  <div class="field" style="left:877px;top:266px;width:250px;height:61px">Last Name</div>
  <div class="field" style="left:616px;top:342px;width:249px;height:61px">Email Address</div>
  <div class="field" style="left:877px;top:342px;width:250px;height:61px">Phone No</div>
  <div class="field" style="left:616px;top:417px;width:511px;height:93px;padding-top:14px">Message</div>
  <div class="btn" style="left:616px;top:530px;width:177px;height:59px">Submit</div>
</section>

<footer class="footer">
  <nav class="nav"><span>HOME</span><span>ABOUT ME</span><span>PADCASTS</span><span>VIDEOS</span><span>CONTACT US</span></nav>
  <div class="copyright">Copyright © 2023 CompanyName  All Rights Reserved</div>
  <div class="social"><span>Brightlane</span><span>chirpbox</span></div>
</footer>

</body>
</html>
```